We need letterhead, Business Cards, and envelops designed. We have attached a design of our logo and a sample of letterhead idea that was started but never perfected, it is only an idea for the letterhead if you can design something better we may love that also we are open to change.
We want a design that looks professional in style. we are a non profit trade association in the construction industry. the green color in the attached design represent green building, and we like that. also if you just want to enhance the letterhead sample that we attached that would be fine also.
Thanks and good luck
also the name that should show on the first business cards should be Morgan Feltwick, Director are web address is www.pvtrn.org

```html
<!DOCTYPE html>
<html lang="en">
<head>
<meta charset="utf-8">
<title>PVTRN Letterhead</title>
<link rel="stylesheet" href="https://fonts.googleapis.com/css2?family=Arimo:wght@400;700&family=Montserrat:wght@300;400&display=swap">
<style>
  :root {
    --backdrop: #e4e4e4;
    --paper: #ffffff;
    --ink: #1c1c1c;
    --ink-soft: #3a3a3a;
    --green: #3f7d1f;
    --green-faint: #e3ebdc;
    --green-mist: #f1f5ee;
    --rule: #111111;
  }
  * { box-sizing: border-box; margin: 0; padding: 0; }
  html, body {
    width: 1200px; height: 909px; overflow: hidden;
    background: var(--backdrop);
  }
  .sheet {
    position: absolute; left: 268px; top: 24px;
    width: 665px; height: 860px;
    background: var(--paper);
    box-shadow: 0 4px 18px rgba(0,0,0,.18);
    overflow: hidden;
    font-family: "Arimo", Arial, sans-serif;
    color: var(--ink);
  }
  .footer-art {
    position: absolute; left: 0; top: 712px; width: 300px; height: 148px;
    background: linear-gradient(160deg, var(--green-mist), var(--green-faint));
  }
  .brand {
    position: absolute; left: 92px; top: 52px;
    display: flex; align-items: center; gap: 10px;
  }
  .brand-mark { width: 18px; height: 18px; background: var(--green); }
  .brand-name {
    font-family: "Arimo", Arial, sans-serif;
    font-weight: 400; font-size: 46px; letter-spacing: 2px; color: var(--ink);
  }
  .letter {
    position: absolute; left: 72px; top: 170px; width: 500px;
    font-size: 10.5px; line-height: 13.5px; color: var(--ink-soft);
  }
  .recipient { margin-bottom: 16px; }
  .salutation { margin-bottom: 12px; }
  .letter p { margin-bottom: 13px; }
  .closing { margin-top: 6px; }
  .signer { margin-top: 30px; color: var(--ink); }
  .footer-lines { position: absolute; left: 0; top: 0; }
  .contact {
    position: absolute; left: 438px; top: 728px;
    font-family: "Montserrat", Arial, sans-serif; font-weight: 300;
    font-size: 10.5px; letter-spacing: 1.6px; line-height: 16px; color: var(--ink);
  }
  .contact li { list-style: none; display: flex; align-items: center; gap: 8px; }
  .contact svg { width: 10px; height: 10px; }
  .address {
    position: absolute; left: 318px; top: 780px;
    font-family: "Montserrat", Arial, sans-serif; font-weight: 300; font-style: normal;
    font-size: 10.5px; letter-spacing: 2.4px; line-height: 16px; color: var(--ink);
  }
</style>
</head>
<body>
<main class="sheet">
  <div class="footer-art" role="img" aria-label="Faint green illustration of buildings and a house roofline"></div>

  <header class="brand">
    <span class="brand-mark"></span>
    <span class="brand-name">PVTRN</span>
  </header>

  <article class="letter">
    <div class="recipient">
      June 26, 2014<br>Trenz Pruca<br>Title<br>Company Name<br>4321 First Street<br>Anytown, State ZIP
    </div>
    <div class="salutation">Dear Trenz,</div>
    <p>Lorem ipsum dolor sit amet, consectetur adipiscing elit, sed eiusmod tempor incidunt ut labore et dolore magna aliqua. Ut enim ad minim veniam, quis nostrud exerc. Irure dolor in reprehend incididunt ut labore et dolore magna aliqua. Ut enim ad minim veniam, quis nostrud exercitation ullamco laboris nisi ut aliquip ex ea commodo consequat. Duis aute irure dolor in reprehenderit in voluptate velit esse molestaie cillum. Tia non ob ea soluad incom dereud facilis est er expedit distinct. Nam liber te conscient to factor tum poen legum odioque civiuda et tam. Neque porro quisquam est qui dolorem ipsum quia dolor sit amet, consectetur adipisci velit, sed quia non numquam eius modi tempora incidunt ut labore et dolore magnam aliquam quaerat voluptatem.</p>
    <p>At vver eos et accusam dignissum qui blandit est praesent. Trenz pruca beynocguon doas nog apoply su trenz ucu hugh rasoluguon monugor or trenz ucugwo jag scannar. Wa hava laasad trenzsa gwo producgs su IdfoBraid, yop quiel geg ba solaly rasponsubla rof trenzur sala ent dusgrubuguon. Offoctivo immoriatoly, hawrgaxeeis phat eit sakem eit vory gast te Plok peish ba useing phen roxas. Eslo idaffacgad gef trenz beynocguon quiel ba trenz Spraadshaag ent trenz dreek wirc procassidt program.</p>
    <p>Plloaso mako nuto uf cakso dodtos anr koop a cupy uf cak vux noaw yerw phuno. Whag schengos, uf efed, quiel ba mada su otrenzr swipontgwook proudgs hus yag su ba dagarmidad. Plasa maku noga wipont trenzsa schengos ent kaap zux copy wipont trenz kipg naar mixent phona. Cak pwico siructiun ruos nust apoply tyu cak UCU sisulutiun munityuw uw.</p>
    <p>Lorem ipsum dolor sit amet, consectetur adipiscing elit. Donec id erat quis metus suscipit mattis. Duis elit elit, venenatis id ullamcorper at, sollicitudin nec eros. Vivamus ultricies dapibus neque et laoreet. Suspendisse massa est, fringilla quis neque a, semper consequat lacus. Aenean et dui hendrerit leo condimentum convallis quis a lacus. Etiam imperdiet dignissim nibh placerat condimentum. Etiam et.</p>
    <div class="closing">Sincerely yours,</div>
    <div class="signer">Urna Semper</div>
  </article>

  <svg class="footer-lines" width="665" height="860" viewBox="0 0 665 860" aria-hidden="true">
    <polygon points="470,816 665,812 665,836 478,836" fill="var(--green)"/>
    <rect x="300" y="836" width="365" height="5" fill="var(--rule)"/>
  </svg>

  <ul class="contact">
    <li><svg viewBox="0 0 10 10"><path d="M2 1l2 2-1 1.5a6 6 0 0 0 2.5 2.5L7 6l2 2-1.5 1.5C4.5 9 1 5.5.5 2z" fill="var(--green)"/></svg>123-456-7890</li>
    <li><svg viewBox="0 0 10 10"><rect x="1" y="3" width="8" height="5" fill="var(--green)"/><rect x="3" y="1" width="4" height="2" fill="var(--green)"/></svg>123-456-7891</li>
    <li><svg viewBox="0 0 10 10"><circle cx="5" cy="5" r="4" fill="none" stroke="var(--green)" stroke-width="1.4"/><path d="M1 5h8M5 1c-2 2-2 6 0 8M5 1c2 2 2 6 0 8" fill="none" stroke="var(--green)" stroke-width=".8"/></svg>www.pvtrn.org</li>
  </ul>

  <address class="address">
    address<br>4321 first street<br>anytown, State ZIP
  </address>
</main>
</body>
</html>
```